Modern Business Card for Larkwell 2018

Our company assumes the best about people. We are creating an online community of entrepreneurs and business leaders who struggle with marketing their business online.

This business card should POP! We recently got a new logo and are launching a new website next month, so our business cards should make a statement that feels:
-Fresh
-Smart
-Trustworthy
-Fun

Target Market(s)

small business owners, entrepreneurs

Industry/Entity Type

Digital Marketing

Contact Information for Business Card

Dimensions: 3.5" x 2"

Font styles to use
Sans Serif

Colors
f37122
ffffff

Requirements
Must have
• We need a business card with a modern, bold design. We will use one side of the card as a lead-generation offer, so text on one side will need to fit up to 140 characters. The business card should stick to our core colors (orange, black, and white).
Nice to have
• We think a vertical "portrait" design could be interesting.
Should not have
• Should not look like a traditional business card. The round icon should stand out from a distance.

```html
<!DOCTYPE html>
<html lang="en">
<head>
<meta charset="utf-8">
<title>Larkwell Business Card</title>
<link rel="stylesheet" href="https://fonts.googleapis.com/css2?family=Open+Sans:wght@400;600;700;800&display=swap">
<style>
  :root {
    --orange: #f37122;
    --white: #ffffff;
    --black: #111111;
    --field: #e9e9e9;
    --backdrop: #2b2b2b;
  }
  * { margin: 0; padding: 0; box-sizing: border-box; }
  html, body {
    width: 1200px; height: 960px; overflow: hidden;
    background: var(--backdrop);
    font-family: "Open Sans", Arial, sans-serif;
  }
  .card {
    position: absolute; left: 250px;
    width: 700px; height: 400px;
    overflow: hidden; border-radius: 4px;
    box-shadow: 0 10px 30px rgba(0,0,0,.45);
  }

  /* Back: lead-generation side */
  .card-back { top: 50px; background: var(--orange); color: var(--white); }
  .back-brand {
    position: absolute; left: 40px; top: 70px; width: 270px;
    text-align: center;
  }
  .brand-dot {
    display: block; width: 46px; height: 46px; margin: 0 auto 12px;
    border-radius: 50%; background: var(--white);
  }
  .back-brand .brand-name {
    font-size: 44px; font-weight: 800; letter-spacing: 1px; line-height: 1;
  }
  .back-brand .tagline {
    font-size: 12px; font-weight: 700; letter-spacing: 1.5px;
    text-transform: uppercase; margin-top: 8px;
  }
  .divider {
    position: absolute; left: 335px; top: 40px; width: 1px; height: 150px;
    background: rgba(255,255,255,.55);
  }
  .offer { position: absolute; left: 365px; top: 36px; width: 300px; }
  .offer-headline {
    font-size: 20px; font-weight: 800; line-height: 1.1; text-transform: uppercase;
  }
  .offer-body { font-size: 15px; line-height: 1.3; margin-top: 10px; }
  .offer-url { font-size: 19px; font-weight: 700; margin-top: 14px; }
  .write-field {
    position: absolute; left: 30px; right: 30px; top: 225px; height: 120px;
    background: var(--field); border-radius: 18px;
    padding: 38px 30px 0;
  }
  .write-line { height: 1px; background: #555; margin-bottom: 36px; }

  /* Front: contact side */
  .card-front { top: 510px; background: var(--white); }
  .front-bg { position: absolute; inset: 0; }
  .front-brand { position: absolute; left: 0; right: 0; top: 48px; text-align: center; }
  .front-brand .brand-name {
    font-size: 64px; font-weight: 800; color: var(--black); letter-spacing: 2px; line-height: 1;
  }
  .front-brand .tagline {
    font-size: 13px; font-weight: 700; color: var(--black);
    letter-spacing: 1.5px; text-transform: uppercase; margin-top: 6px;
  }
  .front-mark {
    position: absolute; left: 305px; top: 165px; width: 90px; height: 90px;
    border-radius: 50%; background: var(--orange); border: 5px solid var(--white);
  }
  .contact {
    position: absolute; left: 0; right: 0; top: 268px; text-align: center; color: var(--white);
  }
  .contact-name { font-size: 24px; font-weight: 800; text-transform: uppercase; }
  .contact-title { font-size: 19px; font-weight: 700; text-transform: uppercase; }
  .contact-email { font-size: 19px; font-weight: 400; }
</style>
</head>
<body>

<section class="card card-back">
  <div class="back-brand">
    <span class="brand-dot"></span>
    <div class="brand-name">LARKWELL</div>
    <div class="tagline">Tell stories that inspire action</div>
  </div>
  <div class="divider"></div>
  <div class="offer">
    <p class="offer-headline">Reach more people.<br>Make more money.<br>Create more impact.</p>
    <p class="offer-body">Get your free Larkwell Starter Package and our marketing guide today at</p>
    <p class="offer-url">Larkwellnow.com/start</p>
  </div>
  <div class="write-field">
    <div class="write-line"></div>
    <div class="write-line"></div>
  </div>
</section>

<section class="card card-front">
  <svg class="front-bg" width="700" height="400" viewBox="0 0 700 400" aria-hidden="true">
    <polygon points="0,150 700,270 700,400 0,400" fill="var(--orange)"/>
  </svg>
  <div class="front-brand">
    <div class="brand-name">LARKWELL</div>
    <div class="tagline">Tell stories that inspire action</div>
  </div>
  <div class="front-mark"></div>
  <div class="contact">
    <p class="contact-name">Dana Whitlock</p>
    <p class="contact-title">Story Marketing Coach</p>
    <p class="contact-email">dana@larkwellnow.com</p>
  </div>
</section>

</body>
</html>
```